ourTradeLoop Webdesign - trading your electronics for cash - helping you clear up clutter

We need web design (and an updated logo) for a new company based in London called "ourTradeLoop". It is a platform that enables users to sell their old electronics for cash, either for themselves or they can donate the cash to charity. In time, we also plan to enable buying of electronics on the site. We specialise in mobile phones, tablets, laptops, and games consoles. Please review brindlo.com, which is a US site with the same business, and also tunefernwick.co.uk, so have a similar business in the UK. We would like to see designs that use the colour red, and that are bold. We currently have a logo, and a WIP site built, but the design needs to be dramatically improved, the right colour mix needs to be chosen to give a clean and modern feel. Please review www.ourtradeloop.com to get an understanding of the work that needs to be improved.

Target Market(s)

People who buy electronics frequently, i.e. upgrade every time a new quince product comes out! These guys usually have a lap top, desk top, tablet and phone.

Industry/Entity Type

Electronics

Logo Text

ourTradeLoop

Number of Pages Required

3 page

Font styles to use
Sans Serif

Colors
ec1f27

Requirements
Must have
• Home page design
• "How-it-works" page design
• Sell page design
• Must use the colour red, and have a secondary/accent colour.

```html
<!DOCTYPE html>
<html lang="en">
<head>
<meta charset="utf-8">
<title>ourTradeLoop – Sell and buy electronics</title>
<link href="https://fonts.googleapis.com/css2?family=Open+Sans:wght@400;600;700;800&family=Montserrat:wght@600;700&display=swap" rel="stylesheet">
<style>
:root{
  --red:#ec1f27;
  --red-dark:#c8161d;
  --ink:#2b2b2b;
  --text:#777;
  --muted:#9a9a9a;
  --line:#e4e4e4;
  --hero:#ece9e3;
  --sand:#efece6;
  --dark:#222;
  --darker:#1a1a1a;
  --blue:#2a7fd4;
  --green:#2bb673;
  --orange:#f5a623;
  --gold:#f2b01e;
}
*{box-sizing:border-box;margin:0;padding:0}
html,body{width:1200px;height:2812px;overflow:hidden}
body{font-family:"Open Sans",Arial,sans-serif;color:var(--ink);background:#fff;position:relative}
h2,h3,h4,.btn{font-family:"Montserrat","Open Sans",sans-serif}
section,header,footer{position:absolute;left:0;width:1200px}
.wrap{position:relative;width:1040px;margin:0 auto;height:100%}
.btn{display:inline-block;font-size:11px;font-weight:700;letter-spacing:.5px;color:#fff;padding:11px 22px;text-transform:uppercase}
.btn-dark{background:var(--dark)}
.btn-red{background:var(--red)}

/* header */
.site-header{top:0;height:80px;background:#fff;border-bottom:1px solid var(--line)}
.brand{position:absolute;left:0;top:22px;display:flex;align-items:center;gap:10px;font-size:24px;font-weight:700;color:var(--red)}
.brand .mark{width:28px;height:28px;background:var(--red)}
.nav{position:absolute;right:0;top:0;display:flex;align-items:center;height:54px;font-size:12px}
.nav a{color:#555;padding:0 18px;height:54px;line-height:54px}
.nav a.active{background:var(--red);color:#fff}
.nav .auth{padding:6px 14px;height:auto;line-height:1.4;color:#fff;margin-left:8px;font-size:11px}
.nav .login{background:var(--red)}
.nav .register{background:var(--blue)}

/* hero */
.hero{top:80px;height:540px;background:var(--hero)}
.hero-card{position:absolute;top:40px;width:440px;text-align:center}
.hero-card.sell{left:40px}
.hero-card.buy{right:40px}
.hero-art{height:300px;width:380px;margin:0 auto;border-radius:6px}
.sell .hero-art{background:radial-gradient(circle at 50% 55%,#e8454b 0,#f3b7b9 45%,var(--hero) 72%)}
.buy .hero-art{background:radial-gradient(circle at 50% 60%,#555 0,#a9a6a0 40%,var(--hero) 72%)}
.hero-card h2{font-size:30px;margin-top:18px;letter-spacing:1px}
.sell h2{color:var(--red)}
.buy h2{color:var(--ink)}
.hero-card p{font-size:11px;color:var(--text);line-height:1.6;margin:10px auto 16px;width:360px}
.hero-arrow{position:absolute;top:240px;width:20px;height:40px}
.hero-arrow.prev{left:12px}.hero-arrow.next{right:12px}

/* section headings */
.sec-title{text-align:center;font-size:24px;font-weight:700;letter-spacing:1px;padding-top:44px}
.sec-title::after{content:"";display:block;width:40px;height:2px;background:var(--red);margin:12px auto 0}
.sec-lead{text-align:center;font-size:11px;color:var(--text);line-height:1.7;width:640px;margin:16px auto 0}

/* how it works */
.how{top:620px;height:420px;background:#fff}
.steps{display:flex;justify-content:space-between;width:900px;margin:50px auto 0}
.step{width:260px;text-align:center}
.step svg{width:64px;height:64px}
.step h4{color:var(--red);font-size:12px;margin:18px 0 10px;letter-spacing:.5px}
.step p{font-size:11px;color:var(--text);line-height:1.6}

/* products */
.products{top:1040px;height:460px;border-top:1px solid var(--line)}
.slider-ctrl{position:absolute;right:0;top:56px;display:flex;gap:4px}
.slider-ctrl span{width:26px;height:20px;border:1px solid var(--line);display:block}
.product-row{display:flex;justify-content:space-between;margin-top:32px}
.product{width:200px;text-align:center}
.product .thumb{height:180px;border:1px solid var(--line);display:flex;align-items:center;justify-content:center}
.product .phone{width:78px;height:150px;border-radius:10px;background:linear-gradient(160deg,#3a3a3a,#111 60%,#4a6fa5)}
.product h4{font-size:11px;margin-top:14px}
.product .price{color:var(--red);font-weight:700;font-size:14px;margin-top:4px}
.rating{display:flex;justify-content:center;align-items:center;gap:6px;font-size:10px;color:var(--muted);margin-top:4px}
.stars{color:var(--gold);letter-spacing:1px}

/* stats band */
.band{top:1500px;height:460px;background:var(--red);color:#fff}
.band-art{position:absolute;left:60px;top:60px;width:300px;height:320px;border-radius:8px;background:radial-gradient(circle at 45% 50%,#fff 0,#f7c5c7 30%,var(--red) 68%)}
.band-copy{position:absolute;left:420px;top:70px;width:560px}
.band-copy h2{font-size:24px;letter-spacing:.5px}
.band-copy p{font-size:11px;line-height:1.75;margin-top:16px;color:#fde3e4}
.stores{display:flex;gap:12px;margin-top:26px}
.store{width:130px;height:40px;background:#111;border-radius:6px}

/* safe selling */
.safe{top:1960px;height:380px;background:var(--sand)}
.safe-copy{position:absolute;left:0;top:50px;width:620px}
.safe-copy h2{font-size:22px;letter-spacing:.5px}
.safe-copy h2::after{content:"";display:block;width:40px;height:2px;background:var(--red);margin-top:12px}
.safe-copy p{font-size:11px;color:var(--text);line-height:1.75;margin-top:16px}
.safe-copy .btns{display:flex;gap:10px;margin-top:24px}
.safe-art{position:absolute;right:20px;top:40px;width:320px;height:300px;border-radius:8px;background:radial-gradient(circle at 55% 50%,#fff 0,#d8d6d0 40%,var(--sand) 72%)}

/* newsletter */
.newsletter{top:2340px;height:80px;background:#fff;border-top:1px solid var(--line)}
.news-row{display:flex;align-items:center;height:80px;font-size:11px;font-weight:700}
.news-row .label{width:300px}
.news-input{width:280px;height:34px;border:1px solid var(--line);font-size:11px;color:var(--muted);font-weight:400;padding:9px 12px}
.news-row .btn{margin-left:-1px;padding:10px 20px}
.follow{margin-left:auto;display:flex;align-items:center;gap:8px}
.follow i{width:26px;height:26px;border-radius:50%;display:block}

/* footer */
.site-footer{top:2420px;height:392px;background:var(--darker);color:#aaa}
.foot-cols{display:flex;gap:0;padding-top:44px}
.foot-col{width:200px;font-size:11px;line-height:2.1}
.foot-col.about{width:280px}
.foot-col h4{color:#fff;font-size:13px;margin-bottom:12px}
.foot-col .f-brand{color:#fff;font-size:24px;font-weight:700;margin-bottom:12px;display:flex;align-items:center;gap:10px}
.foot-col .f-brand .f-mark{width:14px;height:14px;background:var(--red);display:block}
.foot-col.about p{line-height:1.7;width:230px}
.cards{display:flex;gap:6px;margin-top:14px}
.cards i{width:38px;height:24px;background:#3a3a3a;border-radius:3px;display:block}
.contact li{list-style:none;display:flex;gap:10px;align-items:flex-start;margin-bottom:6px;line-height:1.6}
.contact svg{flex:none;margin-top:3px}
.copyright{position:absolute;bottom:0;left:0;width:100%;border-top:1px solid #333;text-align:center;font-size:10px;color:#777;padding:18px 0}
</style>
</head>
<body>

<header class="site-header">
  <div class="wrap">
    <div class="brand"><span class="mark"></span>ourTradeLoop</div>
    <nav class="nav">
      <a class="active">Home</a>
      <a>Product Worth</a>
      <a>Buy</a>
      <a>Sell</a>
      <a class="auth login">Log in</a>
      <a class="auth register">Register</a>
    </nav>
  </div>
</header>

<section class="hero">
  <svg class="hero-arrow prev" viewBox="0 0 20 40"><path d="M16 4 4 20l12 16" fill="none" stroke="#bbb" stroke-width="2"/></svg>
  <svg class="hero-arrow next" viewBox="0 0 20 40"><path d="M4 4l12 16L4 36" fill="none" stroke="#bbb" stroke-width="2"/></svg>
  <div class="wrap">
    <div class="hero-card sell">
      <div class="hero-art" role="img" aria-label="Illustration of a red shopping bag surrounded by phones and tablets"></div>
      <h2>SHELL</h2>
      <p>Sell your old phone, tablet or laptop in a few clicks. Get an instant quote, post it for free and receive your cash fast.</p>
      <span class="btn btn-dark">Sell your gadgets</span>
    </div>
    <div class="hero-card buy">
      <div class="hero-art" role="img" aria-label="Illustration of a smartphone with a small shop and a location pin on its screen"></div>
      <h2>BUY</h2>
      <p>Browse checked and graded devices at fair prices. Every item is tested, cleaned and ready to ship to your door.</p>
      <span class="btn btn-dark">Shop them now</span>
    </div>
  </div>
</section>

<section class="how">
  <h2 class="sec-title">HOW IT WORKS</h2>
  <p class="sec-lead">Choose your device, answer a few quick questions about its condition and accept our offer. Send it to us free of charge and we pay you the same day it arrives.</p>
  <div class="steps">
    <div class="step">
      <svg viewBox="0 0 64 64"><circle cx="32" cy="32" r="30" fill="var(--green)"/><circle cx="32" cy="32" r="16" fill="none" stroke="#fff" stroke-width="3"/><path d="M32 22v10l7 5" fill="none" stroke="#fff" stroke-width="3" stroke-linecap="round"/></svg>
      <h4>FAST &amp; FREE DELIVERY</h4>
      <p>Our standard delivery service is free for all orders, regardless of size and value. Pack it up and drop it off.</p>
    </div>
    <div class="step">
      <svg viewBox="0 0 64 64"><circle cx="32" cy="32" r="30" fill="var(--blue)"/><rect x="20" y="29" width="24" height="18" rx="2" fill="#fff"/><path d="M25 29v-5a7 7 0 0 1 14 0v5" fill="none" stroke="#fff" stroke-width="3"/><circle cx="32" cy="37" r="2.5" fill="var(--blue)"/></svg>
      <h4>SAFE &amp; SECURE PAYMENT</h4>
      <p>Payments go straight to your bank or to a charity of your choice, protected by secure checkout at every step.</p>
    </div>
    <div class="step">
      <svg viewBox="0 0 64 64"><circle cx="32" cy="32" r="30" fill="var(--orange)"/><rect x="19" y="26" width="26" height="20" fill="#fff"/><path d="M17 20h30v7H17z" fill="#fff"/><rect x="30" y="20" width="4" height="26" fill="var(--orange)"/></svg>
      <h4>100% MONEY BACK GUARANTEED</h4>
      <p>If a device you buy is not as described, send it back within thirty days for a full and simple refund.</p>
    </div>
  </div>
</section>

<section class="products">
  <div class="wrap">
    <h2 class="sec-title">PRODUCTS</h2>
    <div class="slider-ctrl"><span></span><span></span></div>
    <p class="sec-lead">Popular devices our customers trade every day. Prices shown are what we pay for working models in good condition.</p>
    <div class="product-row">
      <div class="product">
        <div class="thumb"><div class="phone" role="img" aria-label="Photo of the Lumo G3 phone"></div></div>
        <h4>LUMO G3</h4><div class="price">£ 199.00</div>
        <div class="rating"><span class="stars">★★★★☆</span>12 Reviews</div>
      </div>
      <div class="product">
        <div class="thumb"><div class="phone" role="img" aria-label="Photo of the Orbit 6S phone"></div></div>
        <h4>ORBIT 6S</h4><div class="price">£ 120.00</div>
        <div class="rating"><span class="stars">★★★★☆</span>12 Reviews</div>
      </div>
      <div class="product">
        <div class="thumb"><div class="phone" role="img" aria-label="Photo of the Halden M8 phone"></div></div>
        <h4>HALDEN M8</h4><div class="price">£ 249.00</div>
        <div class="rating"><span class="stars">★★★★☆</span>12 Reviews</div>
      </div>
      <div class="product">
        <div class="thumb"><div class="phone" role="img" aria-label="Photo of the Sorvik Nova Note 5 phone"></div></div>
        <h4>SORVIK NOVA NOTE 5</h4><div class="price">£ 329.00</div>
        <div class="rating"><span class="stars">★★★★☆</span>12 Reviews</div>
      </div>
    </div>
  </div>
</section>

<section class="band">
  <div class="wrap">
    <div class="band-art" role="img" aria-label="Illustration of a hand holding a shopping bag coming out of a smartphone"></div>
    <div class="band-copy">
      <h2>MILLIONS OF DEVICES BOUGHT AND SOLD</h2>
      <p>Since we started, people across the country have cleared their drawers of old phones, tablets, laptops and consoles. Each device we receive is tested, wiped of all personal data and given a second life with a new owner, keeping waste out of landfill.</p>
      <p>Download our app to get instant quotes on the go, track your parcel and see your payment arrive in real time. It only takes a minute to start.</p>
      <div class="stores">
        <span class="store" role="img" aria-label="App download badge"></span>
        <span class="store" role="img" aria-label="Second app download badge"></span>
      </div>
    </div>
  </div>
</section>

<section class="safe">
  <div class="wrap">
    <div class="safe-copy">
      <h2>SAFE &amp; SECURE SELLING &amp; PAYMENTS</h2>
      <p>We treat every device with care. Your data is erased with certified tools, your parcel is tracked from door to door and your money is sent the moment your item passes its check.</p>
      <p>Prefer to give back? Choose to donate all or part of your payment to a charity you love and we will transfer it directly on your behalf.</p>
      <div class="btns"><span class="btn btn-red">Find out more</span><span class="btn btn-dark">Sell your mobile</span></div>
    </div>
    <div class="safe-art" role="img" aria-label="Illustration of a hand holding a smartphone with a card payment on screen"></div>
  </div>
</section>

<section class="newsletter">
  <div class="wrap">
    <div class="news-row">
      <span class="label">GET OUR RECENT UPDATES THROUGH YOUR EMAIL ID</span>
      <span class="news-input">Enter your email id</span>
      <span class="btn btn-red">Subscribe now</span>
      <div class="follow">FOLLOW US
        <i style="background:#3b5998"></i><i style="background:#1da1f2"></i><i style="background:#dd4b39"></i><i style="background:#bd081c"></i>
      </div>
    </div>
  </div>
</section>

<footer class="site-footer">
  <div class="wrap">
    <div class="foot-cols">
      <div class="foot-col about">
        <div class="f-brand"><span class="f-mark"></span>ourTradeLoop</div>
        <p>Sell your old electronics for cash or donate the value to charity. Quick, safe and simple.</p>
        <div class="cards"><i></i><i></i><i></i><i></i></div>
      </div>
      <div class="foot-col"><h4>QUICK LINKS</h4>Home<br>Buy<br>Sell<br>Product Worth<br>How it works<br>Contact</div>
      <div class="foot-col"><h4>EXTRAS</h4>About us<br>Charities<br>Our blog<br>FAQs<br>Careers</div>
      <div class="foot-col"><h4>MY ACCOUNT</h4>Log in<br>Register<br>My orders<br>Payments<br>Help</div>
      <div class="foot-col">
        <h4>CONTACT US</h4>
        <ul class="contact">
          <li><svg width="10" height="14" viewBox="0 0 10 14"><path d="M5 0a5 5 0 0 1 5 5c0 4-5 9-5 9S0 9 0 5a5 5 0 0 1 5-5z" fill="var(--red)"/><circle cx="5" cy="5" r="2" fill="var(--darker)"/></svg>14 Larkmoor Lane,<br>London E2 7QX</li>
          <li><svg width="12" height="12" viewBox="0 0 12 12"><path d="M2 0l2.5 3-1.5 1.5a7 7 0 0 0 4.5 4.5L9 7.5l3 2.5-1.5 2C5 12 0 7 0 1.5z" fill="var(--red)"/></svg>1 800 555 0199</li>
          <li><svg width="12" height="10" viewBox="0 0 12 10"><rect width="12" height="10" fill="var(--red)"/><path d="M0 0l6 5 6-5" fill="none" stroke="var(--darker)"/></svg>info@ourtradeloop.com</li>
        </ul>
      </div>
    </div>
  </div>
  <div class="copyright">© 2016 ourTradeLoop. All Rights Reserved.</div>
</footer>

</body>
</html>
```